Help design website for "Brightwater Civic Advisors" to advance the common good

Here is the Google doc link that lays out the design:

https://files.plumrivet.example/sheet/d/7QmTzR2wLx9KpVbN4hJcY8sEaUoFdG3iXkMnPq5rWt6/edit?usp=sharing

Here is the Google drive folder with the logos and photos: https://vault.plumrivet.example/open?id=4HkWp9LzQe2TxRvN8mBaYc3DsUoJfG6

The testimonials are being gathered and will be shared by Friday, 1/4.

The winner will also have to migrate the coding files to my hosting site.

Thank you for your help! Looking forward to seeing your designs.

Target Market(s)

Prospective clients

Industry/Entity Type

Non Profit

Coding

Coded - Design and coding required

Number of Pages Required

5+ page

Requirements
Must have
• Noted in the Google doc regarding layout.
Nice to have

```html
<!DOCTYPE html>
<html lang="en">
<head>
<meta charset="utf-8">
<title>Brightwater Civic Advisors</title>
<link href="https://fonts.googleapis.com/css2?family=Lato:wght@400;700;900&display=swap" rel="stylesheet">
<style>
:root{
  --blue:#3f8ad3;
  --blue-dark:#2f6fae;
  --ink:#222;
  --text:#333;
  --grey-bg:#ececec;
  --dark:#232323;
  --darker:#141414;
  --white:#fff;
}
*{box-sizing:border-box;margin:0;padding:0}
html,body{width:1200px;height:3939px;overflow:hidden}
body{font-family:"Lato",sans-serif;color:var(--text);background:var(--white);position:relative}
.section{position:absolute;left:0;width:1200px}
.center{text-align:center}
h2{font-weight:700;color:var(--ink);letter-spacing:1px}

/* header */
.site-header{top:0;height:137px;background:var(--white)}
.nav{position:absolute;left:92px;top:66px;display:flex;gap:42px;font-size:13px;font-weight:700;color:#333;letter-spacing:.3px}
.nav a{color:inherit;text-decoration:none;padding-bottom:8px}
.nav a.active{color:var(--blue);border-bottom:2px solid var(--blue)}
.brand{position:absolute;left:830px;top:36px;display:flex;align-items:center;gap:16px}
.brand-mark{width:52px;height:52px;background:var(--blue-dark)}
.brand-name{font-size:21px;font-weight:700;color:#555;letter-spacing:3px;line-height:1.15;text-transform:uppercase}

/* hero */
.hero{top:137px;height:520px}
.hero-photo{position:absolute;inset:0;background:linear-gradient(90deg,#4a4540 0%,#8d7c70 35%,#b7a798 60%,#6d625a 100%)}
.hero-shade{position:absolute;inset:0;background:rgba(0,0,0,.22)}
.hero-title{position:absolute;top:175px;width:100%;text-align:center;color:var(--white);font-size:54px;font-weight:900;line-height:1.08;letter-spacing:.5px}
.hero-dots{position:absolute;top:478px;width:100%;display:flex;justify-content:center;gap:8px}
.hero-dots span{width:13px;height:13px;background:var(--white);border-radius:2px}
.hero-dots span.on{background:var(--blue)}
.hero-curve{position:absolute;left:0;bottom:0}

/* about */
.about{top:657px;height:528px}
.about h2{position:absolute;left:76px;top:105px;font-size:34px}
.about-text{position:absolute;left:76px;top:170px;width:510px;font-size:14.5px;line-height:1.85}
.about-text p{margin-bottom:18px}
.btn{display:inline-block;background:var(--blue);color:var(--white);font-weight:700;font-size:13px;letter-spacing:.5px;text-align:center;text-decoration:none;text-transform:uppercase}
.about .btn{position:absolute;left:76px;top:410px;width:178px;height:42px;line-height:42px}
.about-photo{position:absolute;left:615px;top:98px;width:512px;height:372px;background:linear-gradient(135deg,#3a3a3a,#7e6a5e 55%,#a08978)}

/* services */
.services{top:1185px;height:1030px;background:var(--grey-bg)}
.services h2{position:absolute;top:50px;width:100%;font-size:34px}
.services .lead{position:absolute;top:108px;width:100%;font-size:14px}
.cards{position:absolute;left:76px;top:165px;display:grid;grid-template-columns:repeat(3,330px);column-gap:28px;row-gap:32px}
.card{height:382px;background:var(--blue);color:var(--white);text-align:center}
.card-photo{height:173px}
.card h3{font-size:17px;font-weight:700;text-transform:uppercase;letter-spacing:.5px;line-height:1.3;padding:32px 20px 0}
.card p{font-size:13.5px;line-height:1.6;padding:8px 40px 0}

/* testimonials */
.testimonials{top:2213px;height:410px;background:linear-gradient(90deg,#1e2b3b 0%,#2a4a6e 55%,#3e7fc0 100%);color:var(--white)}
.testimonials h2{position:absolute;top:52px;width:100%;color:var(--white);font-size:34px}
.quote{position:absolute;top:118px;left:175px;width:850px;font-size:18px;line-height:1.6;text-align:center}
.cite-name{position:absolute;top:242px;width:100%;font-size:16px;font-weight:900;letter-spacing:.5px}
.cite-role{position:absolute;top:272px;width:100%;font-size:13.5px}
.t-dots{position:absolute;top:330px;width:100%;display:flex;justify-content:center;gap:10px}
.t-dots span{width:11px;height:11px;border-radius:50%;background:var(--darker)}
.t-dots span.on{background:var(--white)}

/* media */
.media{top:2623px;height:659px}
.media h2{position:absolute;top:48px;width:100%;font-size:34px}
.media .lead{position:absolute;top:106px;width:100%;font-size:14px}
.media-grid{position:absolute;left:76px;top:160px;display:grid;grid-template-columns:repeat(3,330px);column-gap:28px}
.tab{height:63px;background:var(--blue);color:var(--white);font-size:25px;font-weight:700;padding:0 18px;display:flex;align-items:center;justify-content:space-between;letter-spacing:.5px}
.media-photo{height:217px}
.caption{font-size:13.5px;font-weight:700;color:var(--ink);line-height:1.6;margin-top:26px;height:48px}
.media .btn{margin-top:24px;width:130px;height:38px;line-height:38px}

/* consult */
.consult{top:3282px;height:578px;background:var(--dark);color:var(--white)}
.consult h2{position:absolute;top:44px;width:100%;color:var(--white);font-size:33px;font-weight:700}
.consult .lead{position:absolute;top:102px;left:160px;width:880px;font-size:14px;line-height:1.65;text-align:center}
.form{position:absolute;left:254px;top:164px;width:692px}
.row{display:flex;gap:14px;margin-bottom:14px}
.field{flex:1;height:40px;background:var(--white);border-radius:3px;color:#444;font-size:13px;padding:11px 12px}
.field.msg{height:96px}
.submit{position:absolute;left:509px;top:392px;width:182px;height:50px;line-height:50px;font-size:16px}
.note{position:absolute;top:489px;width:100%;font-size:13px}
.note b{color:var(--blue)}

/* footer */
.site-footer{top:3860px;height:79px;background:var(--darker);color:#bbb}
.copyright{position:absolute;left:76px;top:33px;font-size:12px}
.social{position:absolute;right:70px;top:30px;display:flex;gap:14px}
.social span{width:20px;height:20px;border-radius:50%;background:#cfcfcf}
</style>
</head>
<body>

<header class="section site-header">
  <nav class="nav">
    <a class="active" href="#">HOME</a><a href="#">ABOUT</a><a href="#">SERVICES</a><a href="#">TESTIMONIALS</a><a href="#">MEDIA &amp; IMPACT</a><a href="#">CONTACT</a>
  </nav>
  <div class="brand"><span class="brand-mark"></span><span class="brand-name">Brightwater<br>Civic Advisors</span></div>
</header>

<section class="section hero">
  <div class="hero-photo" role="img" aria-label="Group photo of the advisory team standing together indoors"></div>
  <div class="hero-shade"></div>
  <h1 class="hero-title">WELCOME TO<br>BRIGHTWATER CIVIC ADVISORS</h1>
  <div class="hero-dots"><span class="on"></span><span></span><span></span></div>
  <svg class="hero-curve" width="1200" height="40" viewBox="0 0 1200 40"><path d="M0 40 L0 10 Q600 60 1200 0 L1200 40 Z" fill="#fff"/></svg>
</section>

<section class="section about">
  <h2>ABOUT</h2>
  <div class="about-text">
    <p>Brightwater Civic Advisors supports nonprofit organizations and educational institutions to carry out their missions to benefit the wider community.</p>
    <p>Founder Dana Okafor is an educator with a 22-year record of demonstrated achievement and leadership roles in nonprofits and educational institutions. Most recently, she served as Associate Dean of Students in the University and Director of the University Community Service Center at the Lakeshore University.</p>
  </div>
  <a class="btn" href="#">READ MORE</a>
  <div class="about-photo" role="img" aria-label="Portrait of the founder"></div>
</section>

<section class="section services">
  <h2 class="center">OUR SERVICES</h2>
  <p class="lead center">Dana offers consulting services in six areas to support nonprofits and educational institutions.</p>
  <div class="cards">
    <article class="card"><div class="card-photo" role="img" aria-label="Staff members holding colorful signs at a training" style="background:linear-gradient(135deg,#5a3a2e,#a4553f,#3b3b5a)"></div><h3>Staff Professional<br>Development</h3><p>Dana has supervised, coached, and mentored hundreds of staff members, including professionals and students.</p></article>
    <article class="card"><div class="card-photo" role="img" aria-label="Community partners posing together at an event" style="background:linear-gradient(135deg,#2c2a30,#7a6a66,#3b3340)"></div><h3>Community Partnership<br>Development</h3><p>Dana has collaborated with more than 250 nonprofits, schools, government agencies, and businesses with corporate social responsibility...</p></article>
    <article class="card"><div class="card-photo" role="img" aria-label="Group discussion in a crowded room" style="background:linear-gradient(135deg,#6e5040,#a88a72,#4a3a33)"></div><h3>Group Facilitation<br>&amp; Leadership Training</h3><p>Dana has facilitated student groups, experiential learning activities, and dialogues on social justice issues, such as power and privilege...</p></article>
    <article class="card"><div class="card-photo" role="img" aria-label="Large group of program participants cheering outdoors" style="background:linear-gradient(180deg,#a9c4dc,#3f4a55 60%,#2a2f35)"></div><h3>Program Design,<br>Implementation, &amp; Evaluation</h3><p>Dana has launched several programs that take into account best practices, as well as particular institutional cultures, participant demographics...</p></article>
    <article class="card"><div class="card-photo" role="img" aria-label="Speaker addressing an audience in a wood-paneled hall" style="background:linear-gradient(135deg,#6b3d22,#b07a4f,#e2d6c6)"></div><h3>Event Planning</h3><p>Dana has planned events of all sizes that bring together students, staff, faculty, alumni, community partners, leaders and residents for dialogue and service.</p></article>
    <article class="card"><div class="card-photo" role="img" aria-label="Presenter beside a projected slide" style="background:linear-gradient(135deg,#cfd4d8,#8c9aa6,#3c4c5e)"></div><h3>Strategic Planning<br>&amp; Visioning</h3><p>At the Lakeshore University, Dana established and managed a 16-member Advisory Board, including undergraduates, graduate students...</p></article>
  </div>
</section>

<section class="section testimonials">
  <h2 class="center">TESTIMONIALS</h2>
  <p class="quote">“Lorem ipsum dolor sit amet, consectetur adipiscing elit. Quisque elementum tortor nulla, nec tempus tellus ultricies vitae. Phasellus non lacus est. Proin scelerisque sapien eros, laoreet molestie diam varius vitae. Donec et velit eros. Mauris luctus facilisis nisl at hendrerit.”</p>
  <p class="cite-name center">MARCUS ELLERY,</p>
  <p class="cite-role center">Chief Executive Officer, Fairground Collective</p>
  <div class="t-dots"><span class="on"></span><span></span><span></span><span></span><span></span></div>
</section>

<section class="section media">
  <h2 class="center">MEDIA &amp; IMPACT</h2>
  <p class="lead center">Here is the media coverage for the programs and events that Dana oversaw</p>
  <div class="media-grid">
    <div><div class="tab">ARTICLES <svg width="16" height="22" viewBox="0 0 16 22"><path d="M3 2 L13 11 L3 20" stroke="#fff" stroke-width="3" fill="none"/></svg></div><div class="media-photo" role="img" aria-label="Attendees at round tables listening to a speaker" style="background:linear-gradient(135deg,#3a2e28,#8a6e58,#d8cfc6)"></div><p class="caption">Attendees listening to a speaker at the Common Table Dinner Dialogue event...</p><a class="btn" href="#">READ MORE</a></div>
    <div><div class="tab">VIDEOS <svg width="16" height="22" viewBox="0 0 16 22"><path d="M3 2 L13 11 L3 20" stroke="#fff" stroke-width="3" fill="none"/></svg></div><div class="media-photo" role="img" aria-label="Students in a rooftop garden among city buildings" style="background:linear-gradient(180deg,#b9c2c8,#6f8a5a 55%,#3f5a2e)"></div><p class="caption">Students at Riverton City Hall's<br>Rooftop Garden</p><a class="btn" href="#">WATCH VIDEO</a></div>
    <div><div class="tab">PODCASTS <svg width="16" height="22" viewBox="0 0 16 22"><path d="M3 2 L13 11 L3 20" stroke="#fff" stroke-width="3" fill="none"/></svg></div><div class="media-photo" role="img" aria-label="Speaker at a podium welcoming volunteers" style="background:linear-gradient(135deg,#1a1414,#5a3e34,#2a1f1c)"></div><p class="caption">Dana welcoming volunteers for the annual Community Day of Service</p><a class="btn" href="#">LISTEN</a></div>
  </div>
</section>

<section class="section consult">
  <h2 class="center">BOOK A COMPLIMENTARY CONSULTATION</h2>
  <p class="lead">Use the form below to tell Dana about your inquiry, and she will schedule a 30-minute meeting, phone call, or video chat to discuss your project outcomes.</p>
  <div class="form">
    <div class="row"><div class="field">First Name</div><div class="field">Last Name</div></div>
    <div class="row"><div class="field">Email Address</div><div class="field">Subject</div></div>
    <div class="row"><div class="field msg">Message</div></div>
  </div>
  <a class="btn submit" href="#">SUBMIT</a>
  <p class="note center"><b>Note:</b> The submissions should be directed to dana@brightwatercivic.example</p>
</section>

<footer class="section site-footer">
  <p class="copyright">Copyright © 2018. Company Name All Rights Reserved.</p>
  <div class="social" aria-label="Social links"><span></span><span></span><span></span><span></span><span></span></div>
</footer>

</body>
</html>
```